Business Card Design for company

We want new business cards. We'd like something different-- yet still highly professional. Our tagline is Clear direction, lasting results. Stock photos are ok, as long as they are relevant and look upscale.

Target Market(s)

Architecture/Business Management Consulting/Engineering Consulting

Contact Information for Business Card

dark gray background with pops of blue might be good, but you tell me. You're the designers. Rounded corners might be nice, but again, you tell me.

Font styles to use
Serif
Sans Serif

Colors
3276b5
5c5c5c
9d9d9d
fbfbfb

Requirements
Nice to have
• Something different, but still very professional.

```html
<!DOCTYPE html>
<html lang="en">
<head>
<meta charset="utf-8">
<title>Northvale – Business Card</title>
<link rel="stylesheet" href="https://fonts.googleapis.com/css2?family=Montserrat:wght@600;700&family=Open+Sans:wght@400&display=swap">
<style>
  :root {
    --brand-blue: #3276b5;
    --slate: #474b50;
    --mid-gray: #5c5c5c;
    --light-gray: #9d9d9d;
    --paper: #fbfbfb;
    --page-bg: #e6e7e9;
    --white: #ffffff;
  }
  * { margin: 0; padding: 0; box-sizing: border-box; }
  html, body {
    width: 1200px; height: 900px; overflow: hidden;
    background: var(--page-bg);
  }
  .business-card {
    position: absolute; left: 120px; top: 153px;
    width: 960px; height: 594px;
    background: var(--paper);
    box-shadow: 0 10px 30px rgba(0,0,0,0.12);
    display: flex; flex-direction: column;
  }
  .card-brand {
    height: 320px;
    background: linear-gradient(180deg, #f7f7f7 0%, var(--paper) 100%);
    display: flex; align-items: center; justify-content: center; gap: 22px;
    padding-top: 10px;
  }
  .brand-mark {
    width: 34px; height: 34px; background: var(--brand-blue);
  }
  .brand-name {
    font-family: "Montserrat", sans-serif; font-weight: 700;
    font-size: 78px; letter-spacing: 2px; color: var(--mid-gray);
    line-height: 1;
  }
  .accent-rule { height: 7px; background: var(--brand-blue); }
  .card-details {
    flex: 1; background: var(--slate); color: var(--white);
    position: relative;
  }
  .details-row {
    position: absolute; top: 30px; left: 0; right: 0;
    display: flex; justify-content: center;
  }
  .person-block {
    width: 448px; text-align: right; padding-right: 32px;
    font-family: "Open Sans", sans-serif; font-size: 25px; line-height: 35px;
  }
  .person-name {
    font-family: "Montserrat", sans-serif; font-weight: 700;
    font-size: 30px; letter-spacing: 0.5px; line-height: 38px;
  }
  .divider { width: 2px; height: 140px; background: var(--light-gray); margin-top: 2px; }
  .contact-block {
    width: 448px; padding-left: 30px; list-style: none;
    font-family: "Open Sans", sans-serif; font-size: 25px; line-height: 35px;
  }
  .contact-block li { display: flex; align-items: center; gap: 8px; }
  .contact-icon { width: 22px; height: 22px; fill: var(--white); flex: none; }
  .tagline {
    position: absolute; left: 0; right: 0; bottom: 36px; text-align: center;
    font-family: "Montserrat", sans-serif; font-weight: 600; font-size: 25px;
    letter-spacing: 0.3px;
  }
</style>
</head>
<body>
  <div class="business-card">
    <div class="card-brand">
      <span class="brand-mark"></span>
      <span class="brand-name">NORTHVALE</span>
    </div>
    <div class="accent-rule"></div>
    <div class="card-details">
      <div class="details-row">
        <div class="person-block">
          <div class="person-name">DANIEL HARPER</div>
          <div>Managing Director</div>
          <div>12345, Address Goes Here</div>
          <div>Country Name, 123456</div>
        </div>
        <div class="divider"></div>
        <ul class="contact-block">
          <li>
            <svg class="contact-icon" viewBox="0 0 24 24" aria-hidden="true"><path d="M3 9c0-3 4-5 9-5s9 2 9 5v1h-5V8H8v2H3z M6 12h12l2 8H4z M10 14h4v4h-4z"/></svg>
            044-987 654 321
          </li>
          <li>
            <svg class="contact-icon" viewBox="0 0 24 24" aria-hidden="true"><path d="M7 2h10a1 1 0 0 1 1 1v18a1 1 0 0 1-1 1H7a1 1 0 0 1-1-1V3a1 1 0 0 1 1-1zm1 3v12h8V5zm4 13.5a1 1 0 1 0 0 2 1 1 0 0 0 0-2z"/></svg>
            044-987 654 321
          </li>
          <li>
            <svg class="contact-icon" viewBox="0 0 24 24" aria-hidden="true"><path d="M3 6h18v12H3z M4 7l8 6 8-6" stroke="#474b50" stroke-width="1.5"/></svg>
            hello@northvale.com
          </li>
          <li>
            <svg class="contact-icon" viewBox="0 0 24 24" aria-hidden="true"><circle cx="12" cy="12" r="9"/><path d="M8 7c2 0 3 1 2 3s-3 1-3 3 2 2 2 4M15 5c-1 2 1 3 2 4s2 3 0 5" stroke="#474b50" stroke-width="1.6" fill="none"/></svg>
            www.northvale.com
          </li>
        </ul>
      </div>
      <p class="tagline">CLEAR DIRECTION, LASTING RESULTS</p>
    </div>
  </div>
</body>
</html>
```